Modern design company business card design

We are a design oriented construction firm. The owner is an architect and licensed General Contractor and accomplished furniture designer. We do new home construction and large scale remodeling and office design. We would like a design for our new business cards that is clean and modern, but relatable. We like the bright green color of our logo mixed with different shades of grey. We're also open to reinterpreting the logo.

Target Market(s)

Potential design clients,
Construction clients

Industry/Entity Type

Architecture

Contact Information for Business Card

Tall Maple Design | Build Inc. (optional with logo, Inc. optional)Jeffrey MorganOwner (optional)317.555.0148 cell317.431.8056 officejmorgan@greensquareinc.comwww.greensquareinc.com

Font styles to use
Sans Serif
Other font styles liked:
• Avenir

Requirements
Nice to have
• I like designs that have some continuity between the front and back, i.e. similar layouts or graphic elements that wrap around the card. I tend to prefer horizontal over vertical, but that's not a have to. I also tend to prefer white or recycled paper.

```html
<!DOCTYPE html>
<html lang="en">
<head>
<meta charset="utf-8">
<title>Tall Maple Design | Build Inc. — Business Card</title>
<link rel="stylesheet" href="https://fonts.googleapis.com/css2?family=Nunito+Sans:wght@400;600;800&display=swap">
<style>
  :root{
    --bg:#e9e7e3;
    --kraft-light:#c9b8a2;
    --kraft-dark:#ac977f;
    --green-light:#74c978;
    --green-dark:#3aa847;
    --band-grey:#9a9ca3;
    --accent-lime:#d8ee8a;
    --white:#ffffff;
  }
  *{box-sizing:border-box;margin:0;padding:0}
  html,body{width:1200px;height:913px;overflow:hidden;background:var(--bg);
    font-family:"Nunito Sans",Avenir,sans-serif;color:var(--white)}
  .canvas{position:relative;width:1200px;height:913px}
  .card{position:absolute;width:560px;height:320px;border-radius:18px;overflow:hidden;
    background:linear-gradient(135deg,var(--kraft-light),var(--kraft-dark));
    box-shadow:0 10px 26px rgba(0,0,0,.22)}
  .card--front{left:80px;top:130px}
  .card--back{left:560px;top:480px}
  .card__shapes{position:absolute;inset:0;width:100%;height:100%}

  .company{position:absolute;font-weight:600;color:var(--white);
    text-transform:uppercase;letter-spacing:.08em;line-height:1.15}
  .company span{display:block}

  .card--front .company{left:44px;top:128px;font-size:22px}
  .card--back .company{left:0;right:0;top:118px;text-align:center;font-size:38px}

  .person{position:absolute;right:34px;top:30px;text-align:right}
  .person__name{font-weight:800;font-size:21px;letter-spacing:.02em;text-transform:uppercase}
  .person__role{font-size:13px;color:var(--accent-lime);margin-top:2px}

  .contact{position:absolute;right:30px;top:148px;list-style:none;text-align:right}
  .contact li{display:flex;justify-content:flex-end;align-items:center;gap:8px;
    font-size:14px;line-height:22px}
  .contact__icon{width:15px;height:15px;background:var(--white);border-radius:2px;
    display:inline-flex;align-items:center;justify-content:center}
  .contact__icon svg{width:11px;height:11px}
</style>
</head>
<body>
<main class="canvas">

  <section class="card card--front" aria-label="Card front">
    <svg class="card__shapes" viewBox="0 0 560 320" aria-hidden="true">
      <defs>
        <linearGradient id="greenPanel" x1="0" y1="0" x2="0" y2="1">
          <stop offset="0" stop-color="#74c978"/>
          <stop offset="1" stop-color="#3aa847"/>
        </linearGradient>
      </defs>
      <path d="M268 0 C222 90 226 230 306 320 L330 320 C252 230 250 90 296 0 Z" fill="#9a9ca3"/>
      <path d="M296 0 C250 90 252 230 330 320 L560 320 L560 0 Z" fill="url(#greenPanel)"/>
    </svg>

    <p class="company"><span>Tall Maple</span><span>Design Build</span></p>

    <header class="person">
      <h1 class="person__name">Dennis Holloway</h1>
      <p class="person__role">Owner</p>
    </header>

    <ul class="contact">
      <li>317.555.0172
        <span class="contact__icon"><svg viewBox="0 0 12 12"><rect x="2" y="1" width="8" height="10" rx="1" fill="none" stroke="#3aa847" stroke-width="1.4"/><line x1="4" y1="4" x2="8" y2="4" stroke="#3aa847"/></svg></span></li>
      <li>317.555.0148
        <span class="contact__icon"><svg viewBox="0 0 12 12"><path d="M3 1 L5 3 L4 5 C5 7 6 8 7 8 L9 7 L11 9 L9 11 C5 11 1 7 1 3 Z" fill="#3aa847"/></svg></span></li>
      <li>www.tallmapleinc.example
        <span class="contact__icon"><svg viewBox="0 0 12 12"><circle cx="6" cy="6" r="4.5" fill="none" stroke="#3aa847" stroke-width="1.2"/><line x1="1.5" y1="6" x2="10.5" y2="6" stroke="#3aa847"/><ellipse cx="6" cy="6" rx="2" ry="4.5" fill="none" stroke="#3aa847"/></svg></span></li>
      <li>dholloway@tallmapleinc.example
        <span class="contact__icon"><svg viewBox="0 0 12 12"><rect x="1" y="2.5" width="10" height="7" fill="none" stroke="#3aa847" stroke-width="1.2"/><path d="M1 3 L6 7 L11 3" fill="none" stroke="#3aa847"/></svg></span></li>
    </ul>
  </section>

  <section class="card card--back" aria-label="Card back">
    <p class="company"><span>Tall Maple</span><span>Design Build</span></p>
  </section>

</main>
</body>
</html>
```